Milkman leaflet

We are looking for a flyer designed to target new customers. The main benefit that needs highliting is the fact that farmers get more per litre by buying from us than from the larger milk processors.
We are looking for a traditional design which takes readers back to the good old days before supermarkets started destroying small businesses.

Target Market(s)

Families and retired people

Requirements
Must have
• The flyer will be designed as an A5 document with two sides.
At least three pictures
The company logo
Tel: 0121 735 9184
www.brookvalemilk.co.uk

```html
<!DOCTYPE html>
<html lang="en">
<head>
<meta charset="utf-8">
<title>Brookvale Dairies – Milkman Leaflet</title>
<link href="https://fonts.googleapis.com/css2?family=Rokkitt:wght@400;500;600&family=Questrial&family=Arimo:wght@400;700&family=Dancing+Script:wght@500&display=swap" rel="stylesheet">
<style>
  :root {
    --canvas-grey: #a7a9ac;
    --frame-blue: #1b84c3;
    --deep-blue: #1f3f8f;
    --ink: #1d1d1b;
    --paper: #f7f9fc;
    --ray: #dbe6f2;
    --accent-orange: #e4763a;
    --photo-stone: #7a7466;
    --photo-milk: #e9ebe6;
    --photo-snow: #c9cdd3;
    --photo-street: #5c6b4e;
    --photo-print: #c75b8a;
    --recycle-green: #3f9a3a;
  }
  * { box-sizing: border-box; margin: 0; padding: 0; }
  html, body { width: 1200px; height: 825px; overflow: hidden; }
  body { background: var(--canvas-grey); font-family: "Questrial", "Century Gothic", sans-serif; color: var(--ink); position: relative; }

  .leaflet-side {
    position: absolute; top: 19px; width: 555px; height: 787px;
    background: var(--frame-blue); overflow: hidden;
  }
  .side-front { left: 19px; }
  .side-back { left: 626px; }

  .headline {
    position: absolute; left: 11px; top: 10px;
    font-family: "Rokkitt", Georgia, serif; font-weight: 500;
    font-size: 53px; line-height: 51px; letter-spacing: -0.5px;
    color: #fff; white-space: nowrap;
    transform: scaleX(0.86); transform-origin: left top;
  }

  .sheet {
    position: absolute; left: 11px; top: 116px; right: 11px; bottom: 11px;
    background: radial-gradient(ellipse at 45% 55%, var(--paper) 0%, var(--paper) 40%, var(--ray) 100%);
    overflow: hidden;
  }

  .block { position: absolute; }
  .lead { font-size: 17px; line-height: 22px; }
  .body-copy { font-size: 14.5px; line-height: 19px; }
  .body-large { font-size: 17px; line-height: 22px; }

  .subhead {
    font-family: "Rokkitt", Georgia, serif; font-weight: 500;
    font-size: 23px; line-height: 23px; color: var(--ink); margin-bottom: 3px;
  }
  .subhead-blue { color: var(--frame-blue); font-weight: 600; }

  .callout {
    position: absolute; border: 2px solid var(--accent-orange); border-radius: 6px;
    background: #fff; box-shadow: 0 0 0 3px #fff, 2px 3px 6px rgba(0,0,0,.18);
    font-family: "Dancing Script", cursive; color: var(--accent-orange);
    text-align: center; display: flex; align-items: center; justify-content: center;
  }

  .photo { position: absolute; border: 5px solid #fff; box-shadow: 1px 2px 6px rgba(0,0,0,.35); }
  .photo-bottles { background: linear-gradient(160deg, var(--photo-stone), #4b473e 60%, var(--photo-milk) 61%, #b9b6ab); transform: rotate(1.5deg); }
  .photo-snow { background: linear-gradient(180deg, #9ea5ad, var(--photo-snow) 55%, #eef0f2); }
  .photo-print { background: linear-gradient(135deg, var(--photo-print), #e8c65a 50%, #5d8fcf); border-width: 3px; }
  .photo-crate { background: radial-gradient(circle at 40% 60%, #f4f4f0, #d9d6d0 55%, #a84a4a 100%); }
  .photo-van { background: linear-gradient(180deg, var(--photo-street), #8a8f86 55%, #6e6e6e); }

  .float-print { float: right; width: 84px; height: 88px; margin: 0 4px 4px 8px; position: relative; }
  .float-spacer { float: right; width: 0; height: 150px; }
  .art-recycle {
    float: right; clear: right; width: 70px; height: 70px; margin: 0 0 0 6px;
    border-radius: 50%; background: radial-gradient(circle, #bfe3b0, var(--recycle-green));
  }

  .footer { position: absolute; left: 0; right: 0; bottom: 0; height: 56px; }
  .brand {
    position: absolute; left: 12px; top: 10px; display: flex; align-items: center; gap: 6px;
    font-family: "Arimo", Arial, sans-serif; font-weight: 700; font-size: 13px; line-height: 14px;
    color: var(--deep-blue);
  }
  .brand-dot { width: 30px; height: 30px; border-radius: 50%; background: var(--deep-blue); flex: none; }
  .contact {
    position: absolute; right: 12px; top: 20px;
    font-family: "Arimo", Arial, sans-serif; font-weight: 700; font-size: 16px;
    color: var(--frame-blue); white-space: nowrap;
  }
  .contact span + span { margin-left: 14px; }
</style>
</head>
<body>

<section class="leaflet-side side-front">
  <h1 class="headline">MILK DELIVERED FRESH<br>TO YOUR DOORSTEP</h1>
  <div class="sheet">
    <p class="block lead" style="left:12px; top:12px; width:270px;">A regular milk delivery means you never have to worry about queuing up in shops or running out of milk for your morning cuppa or breakfast cereals and you can be confident your milk is fresh when it arrives.</p>

    <div class="photo photo-bottles" role="img" aria-label="Three glass milk bottles on a stone doorstep" style="left:292px; top:-2px; width:236px; height:168px;"></div>

    <div class="callout" style="left:12px; top:176px; width:268px; height:80px; font-size:20px; line-height:24px;">Why collect your milk<br>when you can get it delivered<br>by your local dairy?</div>

    <div class="block" style="left:12px; top:280px; width:268px;">
      <h2 class="subhead">A flexible service</h2>
      <p class="body-copy">Your milkman is there to serve YOU. You can easily arrange your order to suit your requirements and you can alter your order up until 9.00pm the evening before your next delivery. Simple payment options are available, including online payments.</p>
    </div>

    <div class="block" style="left:298px; top:198px; width:226px;">
      <h2 class="subhead">Home milk delivery is “green”</h2>
      <div class="float-spacer"></div>
      <div class="art-recycle" role="img" aria-label="Green recycling symbol around a globe"></div>
      <p class="body-copy">It is nice to know that when you buy milk from the milkman you are doing your bit towards the environment as well. Milk delivered to your door comes in glass bottles which are reusable and recyclable, saving energy and resources.</p>
    </div>

    <div class="photo photo-snow" role="img" aria-label="Milk float making a delivery on a snowy street" style="left:16px; top:474px; width:131px; height:130px;"></div>
    <div class="block" style="left:158px; top:470px; width:366px;">
      <h2 class="subhead subhead-blue">Fresh milk delivered to your door in ALL weathers</h2>
      <p class="body-copy">It’s not just nice weather we deliver your milk. Come wind, rain or snow Brookvale Dairies’ milkman will guarantee that you are supplied with your milk and many other products.</p>
    </div>

    <div class="footer">
      <div class="brand"><span class="brand-dot"></span><span>Brookvale<br>Dairies</span></div>
      <p class="contact"><span>Tel: 0121 735 9184</span><span>www.brookvalemilk.co.uk</span></p>
    </div>
  </div>
</section>

<section class="leaflet-side side-back">
  <h1 class="headline">MILK AND GROCERIES<br>DOORSTEP DELIVERIES</h1>
  <div class="sheet">
    <div class="block" style="left:10px; top:8px; width:354px;">
      <div class="float-print photo photo-print" role="img" aria-label="Stack of popular magazines"></div>
      <h2 class="subhead">The milkman carries other goods too</h2>
      <p class="body-copy">Milkmen sell a lot more than just milk – they offer a whole variety of other products including fruit &amp; veg, juices, pop, eggs, bread and over 250 other products. Brookvale Dairies will also deliver your favourite magazines and the price on the cover is the price you pay, so why not get them delivered to your door?</p>
    </div>
    <div class="photo photo-crate" role="img" aria-label="Hand lifting a glass milk bottle from a crate" style="left:372px; top:6px; width:156px; height:192px;"></div>

    <div class="callout" style="left:12px; top:220px; width:236px; height:62px; font-size:21px; line-height:23px;">Keep it British!<br>Support your local milkman.</div>

    <div class="block" style="left:12px; top:312px; width:250px;">
      <h2 class="subhead subhead-blue" style="white-space:nowrap;">Fair pay for the farmers</h2>
      <p class="body-large">It is reassuring for many customers that all of the farmers who supply our milk are paid a premium above what the larger dairies are paying. If the supermarkets get their way there will eventually be no milk production in the UK and all milk will be imported. We certainly hope this never happens!</p>
    </div>

    <div class="block" style="left:272px; top:228px; width:258px;">
      <h2 class="subhead">The milkman keeps an eye on the community</h2>
      <p class="body-copy">Helping our customers is simply part of the job for our milkmen, many of whom have foiled burglars, spotted house fires or helped people who are injured or ill. It is also reassuring to know that there is always someone keeping an eye on your house while you are on holidays.</p>
    </div>

    <div class="photo photo-van" role="img" aria-label="Milk float driving along a leafy suburban road" style="left:268px; top:490px; width:234px; height:110px;"></div>

    <div class="footer">
      <div class="brand"><span class="brand-dot"></span><span>Brookvale<br>Dairies</span></div>
      <p class="contact"><span>Tel: 0121 735 9184</span><span>www.brookvalemilk.co.uk</span></p>
    </div>
  </div>
</section>

</body>
</html>
```